Poloshirt Packaging

We need a very attractive packaging design for our poloshirts. We are wholesaler of the schoolwear market. See what we currently have. I dont want any specific sizing put on the packaging. One design for all poloshirts (2 sides).
our logo is attached aswell

Target Market(s)

Parents

Requirements
Must have
• Our logo
Should not have
• size or age

```html
<!DOCTYPE html>
<html lang="en">
<head>
<meta charset="utf-8">
<title>Brightwear Poloshirt Packaging</title>
<link href="https://fonts.googleapis.com/css2?family=Questrial&family=Roboto+Condensed:wght@400;700&display=swap" rel="stylesheet">
<style>
  :root {
    --navy: #15375f;
    --red: #e4202e;
    --white: #ffffff;
    --frame: #333333;
  }
  html, body {
    margin: 0;
    padding: 0;
    overflow: hidden;
    background: var(--white);
  }
  .pack-face {
    width: 849px;
    height: 1200px;
    display: block;
  }
  .frame { fill: var(--white); stroke: var(--frame); stroke-width: 1.5; }
  .ribbon { fill: var(--red); stroke: var(--white); stroke-width: 5; stroke-linejoin: miter; }
  .ribbon-tail { fill: var(--red); }
  .ribbon-label {
    font-family: "Roboto Condensed", "Arial Narrow", sans-serif;
    font-weight: 700;
    font-size: 25px;
    fill: var(--white);
  }
  .brand-name {
    font-family: "Questrial", "Century Gothic", sans-serif;
    font-size: 172px;
    fill: var(--navy);
  }
  .product-name {
    font-family: "Roboto Condensed", "Arial Narrow", sans-serif;
    font-weight: 700;
    font-size: 84px;
    fill: var(--red);
  }
  .facts-box { fill: var(--red); }
  .facts-title, .facts-line {
    font-family: "Roboto Condensed", "Arial Narrow", sans-serif;
    font-size: 20.5px;
    fill: var(--white);
  }
  .facts-title { font-weight: 700; }
  .facts-line { font-weight: 400; }
</style>
</head>
<body>
<svg class="pack-face" viewBox="0 0 994 1405" xmlns="http://www.w3.org/2000/svg">
  <rect class="frame" x="1" y="1" width="992" height="1403"/>

  <g class="feature-ribbons">
    <polygon class="ribbon-tail" points="880,298 957,281 950,318 975,345 920,358"/>
    <polygon class="ribbon-tail" points="619,567 672,549 676,602 709,607 634,627"/>
    <polygon class="ribbon" points="629,385 912,310 914,376 629,451"/>
    <polygon class="ribbon" points="634,456 880,391 883,459 634,526"/>
    <polygon class="ribbon" points="680,538 884,470 886,541 683,593"/>

    <text class="ribbon-label" transform="translate(646,424) rotate(-14.8)">SUPERIOR WEIGHT FABRIC</text>
    <text class="ribbon-label" transform="translate(650,497) rotate(-14.8)">EASY CARE - LOW IRON</text>
    <text class="ribbon-label" transform="translate(712,562) rotate(-14.8)">REACTIVE DYES</text>
  </g>

  <text class="brand-name" x="66" y="835" textLength="862" lengthAdjust="spacingAndGlyphs">Brightwear</text>

  <text class="product-name" x="552" y="1007" textLength="378" lengthAdjust="spacingAndGlyphs">POLOSHIRT</text>

  <g class="did-you-know">
    <rect class="facts-box" x="549" y="1074" width="381" height="161"/>
    <text class="facts-title" x="578" y="1102">Did you know</text>
    <text class="facts-line" x="578" y="1131">This Poloshirt Is Sold In 12 Colours</text>
    <text class="facts-line" x="578" y="1160">Reactive Dyed For Superb Colour Fastness</text>
    <text class="facts-line" x="578" y="1189">A Superior Weight Of 210gms</text>
    <text class="facts-line" x="578" y="1218">Strengthened With Twin Needle Stitching</text>
  </g>
</svg>
</body>
</html>
```